professional business card design for technology company

We are a small technology consulting firm, specialising in consulting based around Cloud and Managed services. Our colour scheme is yellow, blue and white, as you can see in the logos. Although we are based in melbourne australia, due to the nature of our work, our clients can be located anywhere. We are looking for a clean, professional, positive look - similar to our company logo

Target Market(s)

small business

Industry/Entity Type

Business

Contact Information for Business Card

eye catching, designed to incorporate some level of raised printing. Must contain website address, phone number, name and job title

Requirements
Must have
• Logo (attached) - use of the same colour scheme

```html
<!DOCTYPE html>
<html lang="en">
<head>
<meta charset="utf-8">
<title>Nubora Business Card</title>
<link href="https://fonts.googleapis.com/css2?family=Arimo:wght@400;700&display=swap" rel="stylesheet">
<style>
  :root {
    --backdrop: #2f3a42;
    --brand-blue: #22a7e0;
    --brand-yellow: #f5d21c;
    --ink: #4a4a4a;
    --ink-dark: #333b40;
    --paper: #ffffff;
  }
  * { margin: 0; padding: 0; box-sizing: border-box; }
  html, body {
    width: 1200px; height: 1000px; overflow: hidden;
    background: var(--backdrop);
    font-family: "Arimo", Arial, sans-serif;
  }
  .canvas {
    position: relative; width: 1200px; height: 1000px;
  }
  .card {
    position: absolute; left: 280px; width: 640px; height: 366px;
    border-radius: 3px;
    box-shadow: 0 12px 30px rgba(0,0,0,0.35);
  }
  .card--front { top: 70px; background: var(--brand-blue); }
  .card--back { top: 520px; background: var(--paper); color: var(--ink); }

  .brand { display: flex; align-items: center; }
  .brand__dot { border-radius: 50%; flex: none; }
  .brand__name { font-weight: 700; letter-spacing: -0.5px; line-height: 1; }

  .card--front .brand {
    position: absolute; left: 0; right: 0; top: 140px; justify-content: center; gap: 18px;
  }
  .card--front .brand__dot { width: 62px; height: 62px; background: var(--paper); }
  .card--front .brand__name { color: var(--paper); font-size: 64px; }

  .card--back .brand { position: absolute; left: 58px; top: 52px; gap: 14px; }
  .card--back .brand__dot { width: 50px; height: 50px; background: var(--brand-blue); }
  .card--back .brand__name { color: var(--ink); font-size: 48px; }
  .website {
    position: absolute; left: 122px; top: 112px;
    color: var(--brand-blue); font-size: 19px; letter-spacing: 0.3px;
  }

  .contacts { position: absolute; left: 132px; top: 178px; list-style: none; }
  .contacts li {
    display: flex; align-items: center; gap: 10px;
    font-size: 20px; font-weight: 700; color: var(--ink-dark);
    height: 30px;
  }
  .contacts svg { width: 20px; height: 20px; flex: none; }
  .address {
    position: absolute; left: 132px; top: 302px;
    font-size: 20px; line-height: 26px; color: var(--ink-dark);
  }
  .person { position: absolute; right: 88px; top: 180px; text-align: right; }
  .person__name { font-size: 21px; color: var(--ink-dark); }
  .person__role { font-size: 17px; color: var(--brand-blue); margin-top: 6px; }
</style>
</head>
<body>
<main class="canvas">
  <section class="card card--front" aria-label="Card front">
    <div class="brand">
      <span class="brand__dot"></span>
      <span class="brand__name">Nubora</span>
    </div>
  </section>

  <section class="card card--back" aria-label="Card back">
    <div class="brand">
      <span class="brand__dot"></span>
      <span class="brand__name">Nubora</span>
    </div>
    <p class="website">www.nubora.com.au</p>

    <ul class="contacts">
      <li>
        <svg viewBox="0 0 20 20" aria-hidden="true"><circle cx="10" cy="10" r="10" fill="#22a7e0"/><rect x="7" y="4.5" width="6" height="11" rx="1.2" fill="none" stroke="#fff" stroke-width="1.4"/></svg>
        123-456-0001
      </li>
      <li>
        <svg viewBox="0 0 20 20" aria-hidden="true"><circle cx="10" cy="10" r="10" fill="#22a7e0"/><path d="M6.5 5.5l2 0 1 2.5-1.3 1a6 6 0 0 0 2.8 2.8l1-1.3 2.5 1v2c0 .6-.5 1-1 1A8.5 8.5 0 0 1 5.5 6.5c0-.5.4-1 1-1z" fill="#fff"/></svg>
        123-456-0002
      </li>
      <li>
        <svg viewBox="0 0 20 20" aria-hidden="true"><circle cx="10" cy="10" r="10" fill="#22a7e0"/><rect x="5" y="8" width="10" height="7" rx="1" fill="#fff"/><rect x="7" y="4.5" width="6" height="4" fill="none" stroke="#fff" stroke-width="1.2"/><rect x="7" y="10" width="6" height="1.2" fill="#22a7e0"/></svg>
        123-456-0003
      </li>
      <li>
        <svg viewBox="0 0 20 20" aria-hidden="true"><circle cx="10" cy="10" r="10" fill="#22a7e0"/><rect x="4.5" y="6" width="11" height="8" rx="1" fill="#fff"/><path d="M4.5 6.5l5.5 4.2 5.5-4.2" fill="none" stroke="#22a7e0" stroke-width="1.2"/></svg>
        name@email.com
      </li>
    </ul>

    <p class="address">Address line 1,<br>City, State, Zip Code</p>

    <div class="person">
      <p class="person__name">Name Goes Here</p>
      <p class="person__role">Position</p>
    </div>
  </section>
</main>
</body>
</html>
```